Sophisticated, clean website reflecting my feminine, playful side to sell my abstract art,

I need a website no more than 3 pages to showcase my paintings, a little about me and some contact info. I do abstracts so looking for something a little edgy, yet feminine and current.
Updates

Hi there, These are some artists websites that I Iike: Marnelvoss.com (I like how airy it is) peterwallombry.com garethpolvens.com (I like how it scrolls) I'll need a place for a photo ( a headshot-i do not have it yet so I'll need to be able to upload that later) as well as an area for my bio. Also, it's important that I will be able to upload any new photos and descriptions easily so it should be user friendly. Lastly, I like in a sunny place so would like to have this seem upbeat and playful as that is how i like to paint. thanks-I'm trying to upload my photos now -

Target Market(s)

ppl ages 35-70 who want large scale art for their homes

Industry/Entity Type

art

Coding

Coded - Design and coding required

Number of Pages Required

3 page

Colors

Designer to choose colors to be used in the design.

Requirements
Must have
• photos of my art, a place for my bio, be easy to reach me. tasteful-nothing too "in your face" -my clients are pretty high end and organized. They like clean lines
Nice to have
• sophisticated background, muted tones in the back-similar clean font throughout-no cursive
Should not have
• too many dark areas. Too many blocks of color. Too serious.

```html
<!DOCTYPE html>
<html lang="en">
<head>
<meta charset="utf-8">
<title>Helena Sorrell Abstracts</title>
<link rel="stylesheet" href="https://fonts.googleapis.com/css2?family=Oswald:wght@300;400&family=Baloo+2:wght@400&display=swap">
<style>
  :root {
    --ink: #111111;
    --paper: #ffffff;
    --footer-bg: #000000;
    --footer-text: #ffffff;
    --peach: #f4b58a;
    --glow: #f7a25a;
    --rule: #555555;
    --art-pink: #e7b9c9;
    --art-rose: #d79aae;
    --art-rust: #a65a3e;
    --art-plum: #5c3346;
    --art-cream: #f1ddd2;
  }
  * { margin: 0; padding: 0; box-sizing: border-box; }
  html, body { width: 1200px; height: 857px; overflow: hidden; background: var(--paper); }
  body { position: relative; color: var(--ink); font-family: "Baloo 2", sans-serif; }

  .hero { position: absolute; left: 0; top: 0; width: 1200px; height: 750px; }

  .brand { position: absolute; left: 42px; top: 13px; display: flex; align-items: flex-start; }
  .brand__mark { width: 78px; height: 98px; background: var(--ink); }
  .brand__text { margin-left: 12px; width: 107px; font-family: "Oswald", sans-serif; font-weight: 300; font-size: 13.5px; letter-spacing: 0.1px; text-transform: uppercase; }
  .brand__name { display: block; margin-top: 17px; line-height: 16px; white-space: nowrap; }
  .brand__rule { display: block; margin-top: 14px; height: 1px; background: var(--rule); }
  .brand__tagline { display: block; margin-top: 15px; line-height: 16px; }

  .nav { position: absolute; top: 40px; left: 404px; display: flex; gap: 24px; }
  .nav a { font-family: "Oswald", sans-serif; font-weight: 300; font-size: 16.5px; color: var(--ink); text-decoration: none; }

  .intro { position: absolute; left: 42px; top: 245px; width: 320px; }
  .intro__text { font-size: 13.4px; line-height: 21px; color: var(--ink); }
  .intro__cta { display: flex; align-items: center; margin-top: 8px; font-family: "Oswald", sans-serif; font-weight: 300; font-size: 15px; color: var(--ink); text-decoration: none; text-transform: uppercase; }
  .intro__cta svg { margin-left: 9px; }

  .slider-dots { position: absolute; left: 44px; top: 366px; display: flex; gap: 15px; }
  .slider-dots span { width: 10px; height: 10px; display: block; }

  .glow { position: absolute; left: 445px; top: 365px; width: 40px; height: 40px; border-radius: 50%;
    background: radial-gradient(circle, var(--glow) 0%, rgba(247,162,90,0.55) 30%, rgba(247,162,90,0) 70%); }

  .scroll-button { position: absolute; left: 42px; top: 538px; width: 151px; height: 151px; }

  .featured-art { position: absolute; left: 600px; top: 0; width: 600px; height: 750px;
    background:
      radial-gradient(circle at 62% 58%, var(--art-rust) 0%, rgba(166,90,62,0.5) 10%, rgba(166,90,62,0) 26%),
      radial-gradient(circle at 75% 22%, rgba(196,130,90,0.7) 0%, rgba(196,130,90,0) 30%),
      radial-gradient(circle at 20% 10%, rgba(92,51,70,0.55) 0%, rgba(92,51,70,0) 32%),
      radial-gradient(circle at 30% 75%, var(--art-cream) 0%, rgba(241,221,210,0) 35%),
      linear-gradient(150deg, var(--art-rose) 0%, var(--art-pink) 45%, #dfa9b5 75%, #c98f86 100%); }

  .site-footer { position: absolute; left: 0; top: 750px; width: 1200px; height: 107px; background: var(--footer-bg); }
  .site-footer p { position: absolute; left: 0; right: 0; top: 78px; text-align: center; color: var(--footer-text); font-size: 12px; }
</style>
</head>
<body>
  <main class="hero">
    <a class="brand" href="#">
      <span class="brand__mark"></span>
      <span class="brand__text">
        <span class="brand__name">Helena Sorrell</span>
        <span class="brand__rule"></span>
        <span class="brand__tagline">Abstracts</span>
      </span>
    </a>

    <nav class="nav">
      <a href="#">Portfolio</a>
      <a href="#">About</a>
      <a href="#">Contact</a>
    </nav>

    <section class="intro">
      <p class="intro__text">Lorem ipsum dolor sit amet, consectetuer adipiscin elit. Aenean commodo ligula eget dolor.Aenean massa. Cum sociis natoque penatibus et magnis dis.</p>
      <a class="intro__cta" href="#">View Work
        <svg width="27" height="6" viewBox="0 0 27 6"><line x1="0" y1="3" x2="25" y2="3" stroke="var(--peach)" stroke-width="1.4"/><path d="M21 0.5 L26 3 L21 5.5" fill="none" stroke="var(--peach)" stroke-width="1.2"/></svg>
      </a>
    </section>

    <div class="slider-dots">
      <span><svg width="10" height="10" viewBox="0 0 10 10"><path d="M5 0.5 L9.5 5 L5 9.5 L0.5 5 Z" fill="var(--ink)"/></svg></span>
      <span><svg width="10" height="10" viewBox="0 0 10 10"><path d="M5 1 L9 5 L5 9 L1 5 Z" fill="none" stroke="var(--ink)" stroke-width="1.4"/></svg></span>
      <span><svg width="10" height="10" viewBox="0 0 10 10"><path d="M5 1 L9 5 L5 9 L1 5 Z" fill="none" stroke="var(--ink)" stroke-width="1.4"/></svg></span>
      <span><svg width="10" height="10" viewBox="0 0 10 10"><path d="M5 1 L9 5 L5 9 L1 5 Z" fill="none" stroke="var(--ink)" stroke-width="1.4"/></svg></span>
      <span><svg width="10" height="10" viewBox="0 0 10 10"><path d="M5 1 L9 5 L5 9 L1 5 Z" fill="none" stroke="var(--ink)" stroke-width="1.4"/></svg></span>
    </div>

    <div class="glow"></div>

    <svg class="scroll-button" viewBox="0 0 151 151">
      <circle cx="75.5" cy="75.5" r="75" fill="none" stroke="var(--ink)" stroke-width="1"/>
      <line x1="59" y1="92" x2="91" y2="60" stroke="var(--ink)" stroke-width="1.1"/>
      <path d="M74 60 L91 60 L91 77" fill="none" stroke="var(--ink)" stroke-width="1.1"/>
    </svg>

    <div class="featured-art" role="img" aria-label="Featured abstract painting: loose rose-like swirls in pink, blush, rust and dark plum brushstrokes"></div>
  </main>

  <footer class="site-footer">
    <p>©2022 Helena Sorrell Art. All rights reserved.</p>
  </footer>
</body>
</html>
```